Homeowners Insurance Provider Website

We are selling homeowners insurance policy / tenants Policy/Flood Insurance in USA in few states and planning expand nationally.

Our target audience are two folds: Customers (Buy policies) and Insurance Agents who wants to work with us to sell our policies to customers. But website should focus 80% on customers and 20% on agents. So, more customer focused user experience. Please note that there is no direct buy option for customers. They always go through insurance agents.

Customer focused, educational that makes buyer journey easy. We don’t want to come off as trying sell something as there is no direct sales involved from website.

Target Market(s)

Homeowners in USA and Insurance agent who sells these insurance.

Industry/Entity Type

Insurance

Number of Pages Required

4 page

Font styles to use
Other font styles liked:
• Open to suggestions

Colors

Designer to choose colors to be used in the design.

Requirements
Must have
• Three most important things: Trustworthy, Authentic, Simple
• Please use colors form logo and grays
• We like: www.hollowmere.com
• https://www.quillfenbrook.com/
• We need Agent Look up tool on home page similar to what is shown on example sites.
• Design:
• Home Page - Open to Ideas
• Insurance (Products) Landing Page - Info similar to: https://www.quillfenbrook.com/insurance/
• Agents Page - https://www.quillfenbrook.com/agents/
• Claims Page - Information similar to: https://www.quillfenbrook.com/claims-center/
• Site Navigation:
• Home
• Insurance
• Claims
• Agents
• About Us
• Contact Us
Nice to have
• Elegant, minimal and clean design that reflects trust and authenticity.
Should not have
• Slider or rotating images - prefer flat design. Not over powering design.

```html
<!DOCTYPE html>
<html lang="en">
<head>
<meta charset="utf-8">
<title>Hearthline Insurance Co. — Home</title>
<link href="https://fonts.googleapis.com/css2?family=Open+Sans:wght@400;600;700&family=Raleway:wght@400;500;600&display=swap" rel="stylesheet">
<style>
:root{
  --red:#e3202f;
  --red-dark:#c81b29;
  --navy:#233c80;
  --navy-deep:#15265a;
  --ink:#1d1d1f;
  --body:#444;
  --grey-bg:#f3f3f3;
  --grey-line:#d0d0d0;
  --panel:#e4e4e6;
  --footer:#1e1e1e;
  --white:#fff;
}
*{box-sizing:border-box;margin:0;padding:0}
html,body{width:1200px;height:2903px;overflow:hidden;background:var(--white)}
body{position:relative;font-family:"Raleway",sans-serif;color:var(--body)}
.abs{position:absolute}
.btn{display:inline-block;font-family:"Open Sans",sans-serif;font-weight:600;font-size:12px;text-transform:uppercase;color:var(--white);text-align:center;letter-spacing:.3px}
.btn-red{background:var(--red)}
.btn-navy{background:var(--navy)}
.btn-white{background:var(--white);color:var(--red)}

/* hero */
.hero{left:0;top:0;width:1200px;height:547px;background:radial-gradient(ellipse at 72% 55%,#4a5670 0%,#26324a 40%,#141c2e 100%)}
.hero-accent{left:690px;top:140px;width:330px;height:400px;background:radial-gradient(ellipse at 50% 60%,rgba(226,196,176,.55),rgba(226,196,176,0) 65%)}
.navbar{left:141px;top:35px;width:918px;height:85px;background:rgba(238,238,240,.9);display:flex;align-items:center;padding:0 22px}
.brand{display:flex;align-items:center;gap:12px;font-family:"Open Sans",sans-serif;font-weight:700;font-size:22px;color:var(--navy);letter-spacing:.5px}
.brand-mark{width:34px;height:34px;background:var(--red)}
.nav{margin-left:auto;display:flex;align-items:center;gap:22px;font-family:"Raleway",sans-serif;font-weight:500;font-size:13px;color:#222}
.nav .active{color:var(--red)}
.nav .cta{background:var(--navy);color:var(--white);padding:8px 10px}
.hero-box{left:141px;top:269px;width:491px;height:144px;background:rgba(232,232,234,.94);border-radius:5px;padding:18px 20px}
.hero-box h1{font-family:"Open Sans",sans-serif;font-weight:700;font-size:25px;line-height:33px;color:#1a1a1a;text-transform:uppercase;letter-spacing:.4px}
.hero-btn{left:164px;top:399px;width:105px;height:29px;line-height:29px}

/* policy circles */
.policy{width:180px;text-align:center}
.policy .ring{width:180px;height:180px;border-radius:50%;background:#9b9ea5;padding:8px;margin:0 auto}
.policy .disc{width:164px;height:164px;border-radius:50%;background:var(--white);display:flex;align-items:center;justify-content:center}
.policy h3{margin-top:22px;font-family:"Open Sans",sans-serif;font-weight:600;font-size:15px;line-height:21px;color:var(--red);text-transform:uppercase}

/* about */
.section-title{font-family:"Open Sans",sans-serif;font-weight:600;font-size:26px;color:var(--ink);text-transform:uppercase;letter-spacing:1px}
.about{left:141px;top:730px;width:617px}
.rule{height:2px;background:var(--grey-line);position:relative;margin-top:16px}
.rule::before{content:"";position:absolute;left:0;top:0;width:62px;height:4px;background:var(--navy)}
.about p{margin-top:20px;font-size:12.5px;line-height:22.5px;color:#333}
.about .btn{margin-top:22px;width:130px;height:29px;line-height:29px}
.quote-box{left:818px;top:720px;width:241px;height:282px;background:#ececec;border:1px solid #d8d8d8}
.quote-box h2{background:var(--navy);color:var(--white);font-family:"Open Sans",sans-serif;font-weight:600;font-size:20px;text-align:center;height:36px;line-height:36px}
.quote-form{padding:14px 14px 0}
.field{height:32px;border:1px solid #d2d2d2;background:#f2f2f2;margin-bottom:6px;font-size:11px;color:#888;padding:9px 10px}
.field.tall{height:52px}
.quote-form .btn{display:block;width:100%;height:32px;line-height:32px;margin-top:10px}

/* split band */
.band-red{left:0;top:1057px;width:600px;height:329px;background:var(--red)}
.band-navy{left:600px;top:1057px;width:600px;height:329px;background:var(--navy)}
.band-col{top:1112px;width:330px;color:var(--white)}
.band-col h3{font-family:"Open Sans",sans-serif;font-weight:700;font-size:17px;margin-bottom:10px}
.band-col p{font-size:12.5px;line-height:21px}
.band-col .btn{margin-top:14px;width:130px;height:29px;line-height:29px}
.band-right{text-align:right}
.band-seal{left:490px;top:1112px;width:220px;height:220px;border-radius:50%;background:var(--white);display:flex;align-items:center;justify-content:center;text-align:center;font-family:"Open Sans",sans-serif;font-weight:700;font-size:17px;line-height:23px;color:var(--navy);letter-spacing:.5px}

/* insurance */
.insurance{left:0;top:1386px;width:1200px;height:627px;background:var(--grey-bg)}
.center-title{width:1200px;text-align:center}
.center-rule{left:292px;width:616px;height:2px;background:#c9c9c9}
.center-rule::before{content:"";position:absolute;left:277px;top:-1px;width:62px;height:4px;background:var(--navy)}
.cards{left:141px;top:1542px;width:918px;height:413px;display:flex}
.card{position:relative;flex:1;overflow:hidden}
.card-photo{position:absolute;inset:0}
.card-body{position:absolute;left:0;right:0;bottom:0;padding:0 24px 28px;text-align:center;color:var(--white)}
.card-body h3{font-family:"Raleway",sans-serif;font-weight:600;font-size:20px}
.card-body .accent{width:42px;height:2px;background:var(--red);margin:10px auto 14px}
.card-body p{font-size:11px;line-height:18px}
.card-actions{display:flex;justify-content:center;gap:12px;margin-top:18px}
.card-actions .btn{width:110px;height:29px;line-height:29px;font-size:11.5px}
.card-actions .btn:last-child{width:132px}
.card.featured .card-body{top:200px;background:rgba(35,60,128,.88);padding-top:24px;margin:0 0}

/* find agent */
.agent{left:0;top:2013px;width:1200px;height:293px;background:var(--navy-deep)}
.agent .section-title{color:var(--white)}
.agent-text{left:290px;top:2138px;width:620px;text-align:center;color:var(--white);font-size:12.5px;line-height:22.5px}
.agent-search{left:439px;top:2234px;display:flex;gap:9px}
.agent-search .input{width:157px;height:29px;background:var(--white);font-size:11px;color:#777;padding:8px 8px}
.agent-search .btn{width:157px;height:29px;line-height:29px}

/* claims & contact */
.claim{left:141px;top:2360px;width:300px;text-align:center}
.claim h2{font-family:"Open Sans",sans-serif;font-weight:600;font-size:26px;color:var(--navy-deep)}
.claim .big{font-family:"Open Sans",sans-serif;font-weight:700;font-size:54px;color:var(--red);line-height:62px;margin-top:2px}
.claim p{font-size:14px;line-height:24px;color:var(--navy-deep);font-weight:500;margin-top:6px}
.claim .btn{margin-top:34px;width:86px;height:29px;line-height:29px}
.divider{left:441px;top:2362px;width:1px;height:200px;background:#ccc}
.contact{left:484px;top:2350px;width:527px}
.contact .rule::before{width:50px}
.contact .rule{margin-top:14px}
.contact small{display:block;font-size:11px;color:#333;margin-top:14px}
.contact-grid{display:grid;grid-template-columns:1fr 1fr;gap:16px 14px;margin-top:10px}
.contact-grid .field{height:31px;background:var(--white);margin:0}
.contact .btn{margin-top:14px;width:86px;height:29px;line-height:29px}

/* footer */
.footer{left:0;top:2618px;width:1200px;height:250px;background:var(--footer);color:#ccc}
.foot-col{top:2658px}
.foot-col h4{font-family:"Raleway",sans-serif;font-weight:500;font-size:16px;color:var(--white)}
.foot-col .line{height:1px;background:#444;margin:10px 0 12px}
.quick-links li{list-style:none;font-size:11px;line-height:21.5px;color:#ddd}
.quick-links li::before{content:"›";color:#888;margin-right:7px}
.quick-links li.current{color:var(--navy)}
.foot-col p{font-size:11px;line-height:17px}
.foot-col strong{display:block;font-weight:600;color:var(--white);font-size:12px;margin-bottom:2px}
.contact-line{display:flex;align-items:center;gap:10px;font-size:13px;color:#ddd;margin-top:14px}
.contact-line.small{font-size:11px}
.news-input{width:172px;height:29px;background:#555;font-size:11px;color:var(--white);padding:8px 10px;margin-top:14px}
.news-btn{margin-top:10px;width:93px;height:28px;line-height:28px;text-transform:none;font-size:12px}
.foot-name{left:860px;top:2690px;width:190px;text-align:center;font-family:"Open Sans",sans-serif;font-weight:600;font-size:24px;line-height:32px;color:#8d8d8d}
.bottom-bar{left:0;top:2868px;width:1200px;height:35px;background:var(--navy);display:flex;align-items:center;padding:0 141px;color:var(--white);font-size:11px;font-weight:600}
.socials{margin-left:auto;display:flex;gap:6px}
.socials span{width:21px;height:21px;background:#3b62c4;border:1px solid #7f9be0}
</style>
</head>
<body>

<!-- Hero -->
<div class="abs hero" role="img" aria-label="Photo of a businessman in a suit holding open hands beneath a glowing house outline"></div>
<div class="abs hero-accent" aria-hidden="true"></div>
<header class="abs navbar">
  <div class="brand"><span class="brand-mark"></span>HEARTHLINE INSURANCE CO.</div>
  <nav class="nav">
    <span class="active">Home</span><span>About Us</span><span>Insurance</span><span>Agents</span><span>Claims</span><span>Contact Us</span><span class="cta">Get a quote</span>
  </nav>
</header>
<div class="abs hero-box"><h1>Get Homeowners Insurance Policy / Tenants Policy/ Flood Insurance in USA</h1></div>
<span class="abs btn btn-red hero-btn">Read More</span>

<!-- Policies -->
<div class="abs policy" style="left:220px;top:459px">
  <div class="ring"><div class="disc">
    <svg width="64" height="60" viewBox="0 0 64 60" fill="none" stroke="#e3202f" stroke-width="3.5"><path d="M10 30 L32 10 L54 30"/><path d="M16 26 V52 H48 V26"/><path d="M26 44 L38 30"/><circle cx="27" cy="32" r="2.5"/><circle cx="37" cy="42" r="2.5"/></svg>
  </div></div>
  <h3>Homeowners<br>Policy</h3>
</div>
<div class="abs policy" style="left:510px;top:459px">
  <div class="ring"><div class="disc">
    <svg width="64" height="60" viewBox="0 0 64 60"><path d="M8 28 L32 8 L56 28 V54 H8 Z" fill="#e3202f"/><circle cx="25" cy="30" r="4" fill="#fff"/><circle cx="39" cy="30" r="4" fill="#fff"/><rect x="21" y="36" width="8" height="14" fill="#fff"/><rect x="35" y="36" width="8" height="14" fill="#fff"/></svg>
  </div></div>
  <h3>Tenants Policy</h3>
</div>
<div class="abs policy" style="left:792px;top:459px">
  <div class="ring"><div class="disc">
    <svg width="64" height="60" viewBox="0 0 64 60"><path d="M10 30 L32 10 L54 30 V40 H10 Z" fill="#e3202f"/><rect x="27" y="28" width="10" height="12" fill="#fff"/><path d="M6 47 q6-5 12 0 t12 0 t12 0 t12 0 t6 0" fill="none" stroke="#e3202f" stroke-width="3"/><path d="M6 54 q6-5 12 0 t12 0 t12 0 t12 0 t6 0" fill="none" stroke="#e3202f" stroke-width="3"/></svg>
  </div></div>
  <h3 style="margin-top:32px">Flood Insurance</h3>
</div>

<!-- About -->
<section class="abs about">
  <h2 class="section-title">About Us</h2>
  <div class="rule"></div>
  <p>Lorem ipsum dolor sit amet, consectetuer adipiscing elit, sed diam nonummy nibh euismod tincidunt ut laoreet dolore magna aliquam erat volutpat. Ut wisi enim ad minim veniam, quis nostrud exerci tation ullamcorper suscipit lobortis nisl ut aliquip ex ea commodo consequat. Duis autem vel eum iriure dolor in hendrerit in vulputate velit esse molestie consequat, vel illum dolore eu feugiat nulla facilisis at vero eros et accumsan et iusto odio dignissim qui blandit praesent luptatum zzril delenit augue duis dolore te feugait nulla facilisi.</p>
  <span class="btn btn-navy">Read More</span>
</section>
<aside class="abs quote-box">
  <h2>Get A Quote</h2>
  <div class="quote-form">
    <div class="field">Name</div>
    <div class="field">Email</div>
    <div class="field">Subject</div>
    <div class="field tall">Message</div>
    <span class="btn btn-navy">Submit</span>
  </div>
</aside>

<!-- Customers / Agents -->
<div class="abs band-red"></div>
<div class="abs band-navy"></div>
<div class="abs band-col" style="left:141px">
  <h3>Customers</h3>
  <p>Lorem ipsum dolor sit amet, consectetuer adipiscing elit, sed diam nonummy nibh euismod tincidunt ut laoreet dolore magna aliquam erat volutpat. Ut wisi enim ad minim veniam, quis nostrud exerci tation ullamcorper suscipit lobortis nisl ut aliquip ex ea commodo consequat. Duis autem vel eum iriure dolor in hendrerit in vulputate velit esse molestie consequat.</p>
  <span class="btn btn-navy">Learn More</span>
</div>
<div class="abs band-seal">HEARTHLINE<br>INSURANCE CO.</div>
<div class="abs band-col band-right" style="left:729px">
  <h3>Agents</h3>
  <p>Lorem ipsum dolor sit amet, consectetuer adipiscing elit, sed diam nonummy nibh euismod tincidunt ut laoreet dolore magna aliquam erat volutpat. Ut wisi enim ad minim veniam, quis nostrud exerci tation ullamcorper suscipit lobortis nisl ut aliquip ex ea commodo consequat. Duis autem vel eum iriure dolor in hendrerit in vulputate velit esse molestie consequat.</p>
  <span class="btn btn-red">Learn More</span>
</div>

<!-- Insurance -->
<div class="abs insurance"></div>
<h2 class="abs section-title center-title" style="top:1434px">Insurance</h2>
<div class="abs center-rule" style="top:1488px"></div>
<div class="abs cards">
  <article class="card">
    <div class="card-photo" role="img" aria-label="Photo of a couple looking around the bright interior of a new home" style="background:linear-gradient(180deg,#d9d6d2 0%,#a9a39c 45%,#2a2a2a 70%,#111 100%)"></div>
    <div class="card-body">
      <h3>Homeowner Policy</h3><div class="accent"></div>
      <p>Lorem ipsum dolor sit amet, consectetuer adipiscing elit, sed diam nonummy nibh euismod tincidunt ut laoreet dolore magna aliquam erat volutpat.</p>
      <div class="card-actions"><span class="btn btn-red">Quote →</span><span class="btn btn-navy">Read More →</span></div>
    </div>
  </article>
  <article class="card featured">
    <div class="card-photo" role="img" aria-label="Photo of a smiling couple reviewing documents together" style="background:linear-gradient(180deg,#bfa58e 0%,#8c7360 45%,#2c3a6e 100%)"></div>
    <div class="card-body">
      <h3>Tenant Policy</h3><div class="accent"></div>
      <p>Lorem ipsum dolor sit amet, consectetuer adipiscing elit, sed diam nonummy nibh euismod tincidunt ut laoreet dolore magna aliquam erat volutpat.</p>
      <div class="card-actions"><span class="btn btn-red">Quote →</span><span class="btn btn-white">Read More →</span></div>
    </div>
  </article>
  <article class="card">
    <div class="card-photo" role="img" aria-label="Photo of a red house tilted over after flood damage, surrounded by trees" style="background:linear-gradient(180deg,#4d6b34 0%,#7a3a30 40%,#2b2220 70%,#111 100%)"></div>
    <div class="card-body">
      <h3>Flood Policy</h3><div class="accent"></div>
      <p>Lorem ipsum dolor sit amet, consectetuer adipiscing elit, sed diam nonummy nibh euismod tincidunt ut laoreet dolore magna aliquam erat volutpat.</p>
      <div class="card-actions"><span class="btn btn-red">Quote →</span><span class="btn btn-navy">Read More →</span></div>
    </div>
  </article>
</div>

<!-- Find an agent -->
<div class="abs agent"></div>
<h2 class="abs section-title center-title" style="top:2062px;color:#fff">Find An Agent</h2>
<div class="abs" style="left:568px;top:2112px;width:64px;height:3px;background:#fff"></div>
<p class="abs agent-text">Lorem ipsum dolor sit amet, consectetuer adipiscing elit, sed diam nonummy nibh euismod tincidunt ut laoreet dolore magna aliquam erat volutpat. Ut wisi enim ad minim veniam, quis nostrud exerci tation ullamcorper suscipit lobortis nisl ut aliquip ex ea commodo consequat.</p>
<div class="abs agent-search"><div class="input">Search...</div><span class="btn btn-red">Find An Agent</span></div>

<!-- Claims & contact -->
<section class="abs claim">
  <h2>Report And Check</h2>
  <div class="big">A Claim</div>
  <p>Login To Report A Claim Or<br>Check Your Claim Status.</p>
  <span class="btn btn-red">Login</span>
</section>
<div class="abs divider"></div>
<section class="abs contact">
  <h2 class="section-title" style="font-size:25px;font-weight:400">Contact Form</h2>
  <div class="rule"></div>
  <small>Please fill up bellow form</small>
  <div class="contact-grid">
    <div class="field">Name</div><div class="field">Email</div>
    <div class="field">Phone</div><div class="field">Message</div>
  </div>
  <span class="btn btn-red">Submit</span>
</section>

<!-- Footer -->
<footer class="abs footer"></footer>
<div class="abs foot-col" style="left:159px;width:100px">
  <h4>Quick Links</h4><div class="line"></div>
  <ul class="quick-links"><li class="current">Home</li><li>About Us</li><li>Insurance</li><li>Agents</li><li>Claims</li><li>Contact Us</li></ul>
</div>
<div class="abs foot-col" style="left:339px;width:190px">
  <h4>Contact Detail</h4><div class="line"></div>
  <p><strong>Hearthline Insurance</strong>Lorem ipsum dolor sit amet, consectetur adipiscing elit, sed do eiusmod</p>
  <div class="contact-line"><svg width="14" height="14" viewBox="0 0 24 24" fill="#3b62c4"><path d="M6.6 10.8a15 15 0 0 0 6.6 6.6l2.2-2.2c.3-.3.7-.4 1-.2 1.1.4 2.3.6 3.6.6.6 0 1 .4 1 1V20c0 .6-.4 1-1 1A17 17 0 0 1 3 4c0-.6.4-1 1-1h3.5c.6 0 1 .4 1 1 0 1.3.2 2.5.6 3.6.1.3 0 .7-.2 1z"/></svg>123.456.7890</div>
  <div class="contact-line small"><svg width="14" height="11" viewBox="0 0 24 18" fill="#3b62c4"><path d="M0 0h24v18H0z"/><path d="M1 1l11 9 11-9" fill="none" stroke="#1e1e1e" stroke-width="2"/></svg>info@hearthline.com</div>
</div>
<div class="abs foot-col" style="left:623px;width:215px">
  <h4>Join Our Newsletter</h4><div class="line"></div>
  <p>Subscribe to our Newsletter to get the latest scoop right to your inbox</p>
  <div class="news-input">Enter Your Email</div>
  <span class="btn btn-red news-btn">Subscribe</span>
</div>
<div class="abs foot-name">HEARTHLINE<br>INSURANCE CO.</div>
<div class="abs bottom-bar">© 2018 Hearthlineinsurance. All Rights Reserved.
  <div class="socials"><span></span><span></span><span></span></div>
</div>

</body>
</html>
```